Broschüren-Design für Pizzalieferdienst
Zielgruppe
Wir sind ein Pizzalieferdienst in Südtirol.
Aufgabenstellung
Es soll eine Broschüre werden, die als Speisekarte dient und wie man sie nicht oft sieht. Ausgefallene Ideen werden bevorzugt.
Um die maximale Kreativität zu fördern wird lediglich das Logo und die Schriftart vorgegeben.
Viel Spass an alle Teilnehmer!

```html
<!DOCTYPE html>
<html lang="de">
<head>
<meta charset="utf-8">
<title>Forno Volante – Speisekarte</title>
<link href="https://fonts.googleapis.com/css2?family=Lobster&family=Ubuntu:wght@400;500&family=Staatliches&display=swap" rel="stylesheet">
<style>
  :root {
    --stage: #e4e4e4;
    --board: #262626;
    --board-light: #323232;
    --accent: #f6a623;
    --ink: #ffffff;
    --ink-soft: #d8d8d8;
    --tag-ink: #1f1f1f;
    --line: rgba(246,166,35,0.75);
    --line-soft: rgba(255,255,255,0.35);
  }
  * { box-sizing: border-box; margin: 0; padding: 0; }
  html, body { width: 1200px; height: 2820px; overflow: hidden; }
  body {
    background: var(--stage);
    font-family: "Ubuntu", sans-serif;
    color: var(--ink);
    position: relative;
  }
  .page {
    position: absolute;
    left: 170px;
    width: 860px;
    height: 860px;
    background: radial-gradient(ellipse at 30% 20%, var(--board-light), var(--board) 70%);
    overflow: hidden;
  }
  .page--cover { top: 60px; }
  .page--inner-left { top: 960px; }
  .page--inner-right { top: 1860px; }

  /* Wordmark: plain name in the text font */
  .wordmark {
    font-family: "Ubuntu", sans-serif;
    font-weight: 500;
    color: var(--ink);
    letter-spacing: 1px;
    white-space: nowrap;
  }
  .cover__wordmark {
    position: absolute;
    top: 80px; left: 0; right: 0;
    text-align: center;
    font-size: 56px;
  }
  .cover__art {
    position: absolute; left: 90px; top: 190px; width: 680px; height: 470px;
    background: radial-gradient(ellipse at 55% 50%, rgba(255,255,255,0.08), rgba(255,255,255,0) 70%);
  }
  .cover__delivery {
    position: absolute; top: 712px; left: 0; right: 0; text-align: center;
    font-size: 27px; color: var(--ink);
  }
  .cover__rule {
    position: absolute; top: 758px; left: 230px; right: 230px;
    border-top: 2px dashed var(--line-soft);
  }
  .cover__claim {
    position: absolute; top: 770px; left: 0; right: 0; text-align: center;
    font-family: "Lobster", cursive; font-size: 38px; color: var(--accent);
  }

  /* Inner pages */
  .header-photo {
    position: absolute; top: 0; left: 0; right: 0; height: 135px;
  }
  .header-photo--food { background: linear-gradient(90deg, #2a1a12 0%, #8a3b1c 35%, #c0622a 60%, #6b2a14 100%); }
  .header-photo--oven { background: linear-gradient(90deg, #3a3a3a 0%, #8c8c8c 45%, #5a5a5a 75%, #3c3c3c 100%); }
  .section-title {
    position: absolute; top: 38px; left: 45px;
    font-family: "Staatliches", sans-serif; font-size: 64px; letter-spacing: 2px; color: var(--ink);
  }
  .header-wordmark {
    position: absolute; top: 50px; right: 48px;
    font-size: 30px;
  }

  .menu {
    position: absolute; top: 160px; left: 45px; right: 45px;
    display: grid; grid-template-columns: repeat(3, 1fr); column-gap: 24px; row-gap: 12px;
  }
  .dish { position: relative; height: 218px; }
  .dish__name {
    display: flex; align-items: center; gap: 8px;
    font-family: "Lobster", cursive; font-weight: 400; font-size: 22px; color: var(--accent);
    white-space: nowrap;
  }
  .dish__name::before { content: ""; width: 22px; border-top: 2px dashed var(--line); }
  .dish__name::after { content: ""; flex: 1; border-top: 2px dashed var(--line); }
  .dish__ingredients {
    margin-top: 4px; font-size: 13px; line-height: 1.3; color: var(--ink-soft); height: 34px;
  }
  .dish__photo {
    position: absolute; top: 74px; left: 42px; width: 122px; height: 122px; border-radius: 50%;
    background: radial-gradient(circle at 45% 45%, #f1c05a 0%, #d9462a 45%, #b8321c 70%, #d69a4e 88%, #b87430 100%);
  }
  .dish__price {
    position: absolute; top: 176px; right: 6px;
    background: var(--accent); color: var(--tag-ink);
    font-weight: 500; font-size: 16px; padding: 4px 10px;
  }
  .row-rule {
    grid-column: 1 / -1; border-top: 2px dashed var(--line-soft); height: 0; margin: -4px 0 4px;
  }
  .sketch {
    position: absolute; right: 40px; bottom: 40px; width: 290px; height: 190px;
    background: radial-gradient(ellipse at 55% 55%, rgba(255,255,255,0.1), rgba(255,255,255,0) 70%);
  }
</style>
</head>
<body>

<section class="page page--cover">
  <p class="wordmark cover__wordmark">Forno Volante</p>
  <div class="cover__art" role="img" aria-label="Strichzeichnung von Pizzazutaten: Tomaten, Käse, Pilze, Chilis und Basilikum"></div>
  <p class="cover__delivery">Aktuelle Lieferzeit: ca. 45 min</p>
  <div class="cover__rule"></div>
  <p class="cover__claim">Scharf auf pizza? dann bist du hier richtig!</p>
</section>

<section class="page page--inner-left">
  <div class="header-photo header-photo--food" role="img" aria-label="Nahaufnahme einer belegten Pizza"></div>
  <h2 class="section-title">PIZZA</h2>
  <div class="menu">
    <article class="dish"><h3 class="dish__name">Margherita</h3><p class="dish__ingredients">Tomatensauce, Mozzarella, Origano</p><div class="dish__photo" role="img" aria-label="Pizza Margherita"></div><span class="dish__price">6.5 €</span></article>
    <article class="dish"><h3 class="dish__name">Scharfe Salami</h3><p class="dish__ingredients">Tomatensauce, Mozzarella, scharfe Salami, Origano</p><div class="dish__photo" role="img" aria-label="Pizza mit scharfer Salami"></div><span class="dish__price">6.5 €</span></article>
    <article class="dish"><h3 class="dish__name">Thunfisch-Zwiebel</h3><p class="dish__ingredients">Tomatensauce, Mozzarella, Thunfisch, Zwiebel, Origano</p><div class="dish__photo" role="img" aria-label="Pizza mit Thunfisch und Zwiebeln"></div><span class="dish__price">6.5 €</span></article>
    <div class="row-rule"></div>
    <article class="dish"><h3 class="dish__name">Margherita</h3><p class="dish__ingredients">Tomatensauce, Mozzarella, Origano</p><div class="dish__photo" role="img" aria-label="Pizza Margherita"></div><span class="dish__price">6.5 €</span></article>
    <article class="dish"><h3 class="dish__name">Scharfe Salami</h3><p class="dish__ingredients">Tomatensauce, Mozzarella, scharfe Salami, Origano</p><div class="dish__photo" role="img" aria-label="Pizza mit scharfer Salami"></div><span class="dish__price">6.5 €</span></article>
    <article class="dish"><h3 class="dish__name">Thunfisch-Zwiebel</h3><p class="dish__ingredients">Tomatensauce, Mozzarella, Thunfisch, Zwiebel, Origano</p><div class="dish__photo" role="img" aria-label="Pizza mit Thunfisch und Zwiebeln"></div><span class="dish__price">6.5 €</span></article>
    <div class="row-rule"></div>
    <article class="dish"><h3 class="dish__name">Margherita</h3><p class="dish__ingredients">Tomatensauce, Mozzarella, Origano</p><div class="dish__photo" role="img" aria-label="Pizza Margherita"></div><span class="dish__price">6.5 €</span></article>
    <article class="dish"><h3 class="dish__name">Scharfe Salami</h3><p class="dish__ingredients">Tomatensauce, Mozzarella, scharfe Salami, Origano</p><div class="dish__photo" role="img" aria-label="Pizza mit scharfer Salami"></div><span class="dish__price">6.5 €</span></article>
    <article class="dish"><h3 class="dish__name">Thunfisch-Zwiebel</h3><p class="dish__ingredients">Tomatensauce, Mozzarella, Thunfisch, Zwiebel, Origano</p><div class="dish__photo" role="img" aria-label="Pizza mit Thunfisch und Zwiebeln"></div><span class="dish__price">6.5 €</span></article>
  </div>
</section>

<section class="page page--inner-right">
  <div class="header-photo header-photo--oven" role="img" aria-label="Schwarzweißfoto eines Pizzaofens"></div>
  <p class="wordmark header-wordmark">Forno Volante</p>
  <div class="menu">
    <article class="dish"><h3 class="dish__name">Margherita</h3><p class="dish__ingredients">Tomatensauce, Mozzarella, Origano</p><div class="dish__photo" role="img" aria-label="Pizza Margherita"></div><span class="dish__price">6.5 €</span></article>
    <article class="dish"><h3 class="dish__name">Scharfe Salami</h3><p class="dish__ingredients">Tomatensauce, Mozzarella, scharfe Salami, Origano</p><div class="dish__photo" role="img" aria-label="Pizza mit scharfer Salami"></div><span class="dish__price">6.5 €</span></article>
    <article class="dish"><h3 class="dish__name">Thunfisch-Zwiebel</h3><p class="dish__ingredients">Tomatensauce, Mozzarella, Thunfisch, Zwiebel, Origano</p><div class="dish__photo" role="img" aria-label="Pizza mit Thunfisch und Zwiebeln"></div><span class="dish__price">6.5 €</span></article>
    <div class="row-rule"></div>
    <article class="dish"><h3 class="dish__name">Margherita</h3><p class="dish__ingredients">Tomatensauce, Mozzarella, Origano</p><div class="dish__photo" role="img" aria-label="Pizza Margherita"></div><span class="dish__price">6.5 €</span></article>
    <article class="dish"><h3 class="dish__name">Scharfe Salami</h3><p class="dish__ingredients">Tomatensauce, Mozzarella, scharfe Salami, Origano</p><div class="dish__photo" role="img" aria-label="Pizza mit scharfer Salami"></div><span class="dish__price">6.5 €</span></article>
    <article class="dish"><h3 class="dish__name">Thunfisch-Zwiebel</h3><p class="dish__ingredients">Tomatensauce, Mozzarella, Thunfisch, Zwiebel, Origano</p><div class="dish__photo" role="img" aria-label="Pizza mit Thunfisch und Zwiebeln"></div><span class="dish__price">6.5 €</span></article>
    <div class="row-rule"></div>
    <article class="dish"><h3 class="dish__name">Margherita</h3><p class="dish__ingredients">Tomatensauce, Mozzarella, Origano</p><div class="dish__photo" role="img" aria-label="Pizza Margherita"></div><span class="dish__price">6.5 €</span></article>
  </div>
  <div class="sketch" role="img" aria-label="Kreidezeichnung eines Pizzastücks"></div>
</section>

</body>
</html>
```